We are a recruitment company based in Norwich/Cambridge England.
I have included our company logo which we want to remain the same.

What we are looking for is a new creative Business card which will really stand out!!

Contact Information for Business Card

Harriet Dunmore
email: Harriet@plavex.co.uk
Address: Brackwell House
Fenmoor Enterprise Park
Partridge Way
Norwich
QB9 3KX
Tel:01632 960418

```html
<!DOCTYPE html>
<html lang="en">
<head>
<meta charset="utf-8">
<title>Plavex Business Card</title>
<link href="https://fonts.googleapis.com/css2?family=Lato:wght@400;700&family=Roboto:wght@400&display=swap" rel="stylesheet">
<style>
  :root {
    --backdrop: #2b2b2b;
    --brand-green: #8dc63f;
    --brand-grey: #8e8a8f;
    --paper: #f2f2f2;
    --white: #ffffff;
  }
  * { margin: 0; padding: 0; box-sizing: border-box; }
  html, body { width: 1200px; height: 960px; overflow: hidden; }
  body { background: var(--backdrop); position: relative; font-family: "Lato", sans-serif; }

  .card { position: absolute; width: 600px; height: 343px; overflow: hidden; }
  .card-front { left: 322px; top: 108px; background: var(--brand-green); }
  .card-back { left: 320px; top: 493px; background: var(--brand-grey); }

  .front-shape { position: absolute; inset: 0; }

  .contact { position: absolute; left: 26px; top: 74px; color: var(--white); font-weight: 700; }
  .contact-name { font-size: 19px; line-height: 22px; text-transform: uppercase; }
  .contact-role { font-size: 14px; line-height: 18px; text-transform: uppercase; margin-bottom: 10px; }
  .contact-address { font-size: 13px; line-height: 16px; margin-bottom: 8px; }
  .contact-list { list-style: none; font-size: 14px; line-height: 19px; }
  .contact-list li { display: flex; align-items: center; gap: 9px; }
  .contact-list svg { width: 13px; height: 13px; flex: none; }

  .brand { position: absolute; left: 305px; top: 148px; display: flex; align-items: center; gap: 12px; }
  .brand-dot { width: 40px; height: 40px; border-radius: 50%; background: var(--brand-green); }
  .brand-name { font-size: 42px; font-weight: 700; color: var(--brand-grey); line-height: 1; }

  .back-brand { position: absolute; left: 0; right: 0; top: 110px; display: flex; justify-content: center; align-items: center; gap: 18px; }
  .back-dot { width: 70px; height: 70px; border-radius: 50%; background: var(--white); }
  .back-name { font-size: 60px; font-weight: 700; color: var(--white); line-height: 1; }
  .back-web { position: absolute; left: 0; right: 0; top: 300px; text-align: center; color: var(--white); font-family: "Roboto", sans-serif; font-size: 14px; letter-spacing: 4.5px; }
</style>
</head>
<body>
  <section class="card card-front">
    <svg class="front-shape" viewBox="0 0 600 343" aria-hidden="true">
      <path d="M505 0 C300 50 190 200 240 343 H600 V0 Z" fill="var(--brand-grey)"/>
      <path d="M505 0 C320 60 218 210 256 343 H600 V0 Z" fill="var(--paper)"/>
    </svg>
    <div class="contact">
      <p class="contact-name">Harriet Dunmore</p>
      <p class="contact-role">CEO/Founder</p>
      <p class="contact-address">Brackwell House, Fenmoor Enterprise Park<br>Partridge Way, Norwich QB9 3KX</p>
      <ul class="contact-list">
        <li><svg viewBox="0 0 16 16"><path fill="#fff" d="M3 1l3 3-1.5 2a9 9 0 0 0 5.5 5.5L12 10l3 3-2 2C7 15 1 9 1 3z"/></svg>01632 960418</li>
        <li><svg viewBox="0 0 16 16"><path fill="#fff" d="M1 3h14v10H1z M2 4l6 5 6-5" stroke="var(--brand-green)" stroke-width="1"/></svg>Harriet@plavex.co.uk</li>
        <li><svg viewBox="0 0 16 16"><circle cx="8" cy="8" r="7" fill="#fff"/><path d="M1 8h14M8 1c-3 3-3 11 0 14M8 1c3 3 3 11 0 14" stroke="var(--brand-green)" fill="none"/></svg>www.plavex.co.uk</li>
      </ul>
    </div>
    <div class="brand">
      <span class="brand-dot"></span>
      <span class="brand-name">Plavex</span>
    </div>
  </section>

  <section class="card card-back">
    <div class="back-brand">
      <span class="back-dot"></span>
      <span class="back-name">Plavex</span>
    </div>
    <p class="back-web">www.plavex.co.uk</p>
  </section>
</body>
</html>
```